Stylish Business Cards Wanted

- DOUBLE SIDED Design Required -

High end, edgy cards for a corporate and personal stylist. Must include logo,
Name: Belinda Harwick
Title: Director and Stylist
telephone : +61 8 7142 5809
email: belinda@theloombriefing.example
website: theloombriefing.example
Tag: Corporate Workwear & Uniform Specialist | Personal Stylist
Would like nice icons for telephone, email, website

Target Market(s)

Businesses wanting stylish uniforms, people wanting stylish wardrobes

Industry/Entity Type

Corporate Workwear Stylist

Contact Information for Business Card

I would like black, white and gold foiling incorporated in the design - possibly a touch of the other colours on my branding guide attached Name: Belinda Harwick Title: Director and Stylist telephone : +61 8 7142 5809 email: belinda@theloombriefing.example website: theloombriefing.example Tag: Corporate Workwear & Uniform Specialist | Personal Stylist Would like nice icons for telephone, email, website

Font styles to use
Other font styles liked:
• Raleway

Colors

Designer to choose colors to be used in the design.

Requirements
Must have
• Gold foil accents

```html
<!DOCTYPE html>
<html lang="en">
<head>
<meta charset="utf-8">
<title>The Loom Briefing – Business Cards</title>
<link href="https://fonts.googleapis.com/css2?family=Raleway:wght@500;600;700;800&family=Roboto:wght@400;500&display=swap" rel="stylesheet">
<style>
  :root {
    --page: #1c1c1c;
    --ink: #232323;
    --paper: #ffffff;
    --gold: #e4bd52;
    --gold-deep: #c9962f;
    --gold-light: #f0d58a;
  }
  * { margin: 0; padding: 0; box-sizing: border-box; }
  html, body {
    width: 1200px; height: 988px; overflow: hidden;
    background: var(--page);
  }
  .canvas {
    position: relative; width: 1200px; height: 988px;
    display: flex; flex-direction: column; align-items: center; justify-content: center; gap: 44px;
  }
  .card {
    position: relative; width: 700px; height: 400px;
    border-radius: 22px; overflow: hidden;
  }
  /* Front */
  .card-front {
    background: var(--ink);
    display: flex; flex-direction: column; align-items: center; justify-content: center;
  }
  .brand-name {
    font-family: "Raleway", sans-serif; font-weight: 700;
    letter-spacing: 1px; white-space: nowrap;
  }
  .card-front .brand-name { color: var(--paper); font-size: 50px; margin-top: 20px; }
  .tagline {
    margin-top: 70px;
    font-family: "Raleway", sans-serif; font-weight: 500;
    color: var(--gold); font-size: 19px; letter-spacing: 0.3px;
  }
  /* Back */
  .card-back { background: var(--paper); }
  .card-back .wave { position: absolute; inset: 0; }
  .card-back .brand-name {
    position: absolute; left: 56px; top: 118px;
    color: var(--ink); font-size: 38px;
  }
  .contact {
    position: absolute; right: 34px; top: 178px;
    text-align: right; font-family: "Roboto", sans-serif; color: var(--paper);
  }
  .contact-name {
    font-family: "Raleway", sans-serif; font-weight: 800;
    color: var(--gold); font-size: 24px; letter-spacing: 0.5px; text-transform: uppercase;
  }
  .contact-title { font-size: 16px; margin-top: 2px; }
  .contact-list { list-style: none; margin-top: 16px; }
  .contact-list li {
    display: flex; align-items: center; justify-content: flex-end; gap: 9px;
    font-size: 16px; line-height: 27px;
  }
  .contact-list .accent { color: var(--gold); }
  .icon { width: 17px; height: 17px; flex: none; }
</style>
</head>
<body>
<main class="canvas">

  <section class="card card-front" aria-label="Business card front">
    <h1 class="brand-name">The Loom Briefing</h1>
    <p class="tagline">Corporate Workwear &amp; Uniform Specialist | Personal Stylist</p>
  </section>

  <section class="card card-back" aria-label="Business card back">
    <svg class="wave" viewBox="0 0 700 400" preserveAspectRatio="none" aria-hidden="true">
      <defs>
        <linearGradient id="goldFoil" x1="0" y1="0" x2="1" y2="0">
          <stop offset="0" stop-color="var(--gold-deep)"/>
          <stop offset="0.3" stop-color="var(--gold-light)"/>
          <stop offset="0.55" stop-color="var(--gold)"/>
          <stop offset="1" stop-color="var(--gold)"/>
        </linearGradient>
      </defs>
      <path d="M0,342 C230,330 330,300 420,200 C500,112 600,98 700,96 L700,400 L0,400 Z" fill="var(--ink)"/>
      <path d="M0,326 C230,314 324,286 412,188 C494,96 598,82 700,80" fill="none" stroke="url(#goldFoil)" stroke-width="9"/>
      <path d="M0,312 C120,306 200,296 268,268" fill="none" stroke="url(#goldFoil)" stroke-width="4"/>
    </svg>

    <h2 class="brand-name">The Loom Briefing</h2>

    <div class="contact">
      <p class="contact-name">Belinda Harwick</p>
      <p class="contact-title">Director and Stylist</p>
      <ul class="contact-list">
        <li>+61 8 7142 5809
          <svg class="icon" viewBox="0 0 24 24" aria-label="Phone"><circle cx="12" cy="12" r="12" fill="var(--gold)"/><path d="M8 6.5l2 0 1 3-1.5 1.2a7 7 0 0 0 3.8 3.8l1.2-1.5 3 1v2a1.5 1.5 0 0 1-1.6 1.5A11 11 0 0 1 6.5 8.1 1.5 1.5 0 0 1 8 6.5z" fill="var(--ink)"/></svg>
        </li>
        <li>belinda@theloombriefing.example
          <svg class="icon" viewBox="0 0 24 24" aria-label="Email"><circle cx="12" cy="12" r="12" fill="var(--gold)"/><rect x="6" y="8" width="12" height="8.5" rx="1" fill="var(--ink)"/><path d="M6.5 8.6l5.5 4.2 5.5-4.2" fill="none" stroke="var(--gold)" stroke-width="1.2"/></svg>
        </li>
        <li><span>www.<span class="accent">theloombriefing.example</span></span>
          <svg class="icon" viewBox="0 0 24 24" aria-label="Website"><circle cx="12" cy="12" r="12" fill="var(--gold)"/><circle cx="12" cy="12" r="6.5" fill="none" stroke="var(--ink)" stroke-width="1.4"/><ellipse cx="12" cy="12" rx="2.8" ry="6.5" fill="none" stroke="var(--ink)" stroke-width="1.2"/><path d="M5.5 12h13" stroke="var(--ink)" stroke-width="1.2"/></svg>
        </li>
      </ul>
    </div>
  </section>

</main>
</body>
</html>
```